Tabloid Magazine Flyer Class Action Lawsuit

Create a bold, 2-page 8.5" x 11" flyer with the look and feel of a tabloid exposé — loud, sensational, and impossible to ignore. Use bold fonts, dramatic headlines, and high-contrast colors (red, black, white, deep blue). Fill every inch of space — no white space, no subtlety. Use the provided images prominently. Page 1 should grab attention with a shocking headline, impactful image, and strong call to action. Page 2 should stack bold subheadings and explosive bullet points. Emphasize urgency, outrage, and grassroots power. This flyer is meant to rally a community.
Updates

Need to extend because we haven't received a design that meets our needs

Target Market(s)

All instructions and content are in the attached word doc

Industry/Entity Type

Requirements
Must have
• All instructions and content are in the attached word doc
Nice to have
Should not have

```html
<!DOCTYPE html>
<html lang="en">
<head>
<meta charset="utf-8">
<title>Seaview Park Community Flyer</title>
<link rel="stylesheet" href="https://fonts.googleapis.com/css2?family=Bebas+Neue&family=Oswald:wght@600;700&family=Poppins:wght@500;600;700;800&display=swap">
<style>
:root{
  --stage:#9c9c9c;
  --red:#e01b1b;
  --blue:#135a9e;
  --sky:#1c7fd9;
  --navy:#142e5c;
  --navy-2:#1c3f73;
  --ink:#231f20;
  --white:#ffffff;
  --yellow:#f7e51b;
}
*{margin:0;padding:0;box-sizing:border-box}
html,body{width:1200px;height:2937px;overflow:hidden;background:var(--stage)}
body{position:relative;font-family:'Poppins',sans-serif}
.page{position:absolute;left:97px;width:1007px;height:1294px;background:var(--white);overflow:hidden;box-shadow:0 2px 10px rgba(0,0,0,.25)}
.page-one{top:104px}
.page-two{top:1488px}
.blk{position:absolute}
.center{position:absolute;left:0;width:100%;text-align:center;white-space:nowrap}
.photo{position:absolute;border:7px solid var(--white)}

/* page one */
.brand{left:0;top:0;width:426px;height:215px;display:flex;align-items:center;justify-content:center}
.brand-name{font-family:'Poppins',sans-serif;font-weight:800;font-size:40px;line-height:1.15;color:var(--navy);text-align:center}
.headline-red{left:426px;top:0;width:581px;height:460px;background:var(--red)}
.headline{left:426px;top:40px;width:581px;padding-left:38px;font-family:'Bebas Neue',sans-serif;color:var(--white);font-size:96px;line-height:.76;letter-spacing:1px;white-space:nowrap}
.band-blue{left:0;top:455px;width:1007px;height:260px;background:var(--blue)}
.hero-photo{left:48px;top:216px;width:911px;height:353px;background:linear-gradient(180deg,#1b2744 0%,#3a4a6a 22%,#a1785a 48%,#6f5a50 68%,#4a4a52 100%)}
.alarm{top:580px;font-weight:700;font-size:40px;line-height:44px;color:var(--white)}
.help-box{left:238px;top:686px;width:531px;height:66px;background:var(--red);color:var(--white);font-weight:800;font-size:44px;line-height:66px;text-align:center}
.join{font-weight:800;font-size:38px;color:var(--ink);line-height:44px}
.council{font-family:'Oswald',sans-serif;font-weight:700;font-size:54px;color:var(--red);line-height:60px;letter-spacing:.5px}
.date-row{position:absolute;left:0;width:100%;height:72px;display:flex;align-items:center;justify-content:center;gap:14px}
.date-main{font-weight:800;font-size:66px;color:var(--blue);line-height:72px}
.date-year{font-weight:800;font-size:66px;color:var(--ink);line-height:72px;margin-left:10px}
.time-pill{display:flex;align-items:center;gap:14px;background:var(--sky);border-radius:36px;height:70px;padding:0 26px 0 14px;color:var(--white);font-weight:800;font-size:62px;margin-left:6px}
.venue{position:absolute;left:0;width:100%;display:flex;align-items:center;justify-content:center;gap:10px;font-weight:700;font-size:30px;color:var(--ink)}
.band-red-foot{left:0;top:1139px;width:1007px;height:155px;background:var(--red)}
.claim-box{left:50px;top:996px;width:907px;height:198px;background:var(--navy)}
.claim-strip{left:50px;top:996px;width:907px;height:49px;background:var(--blue);color:var(--white);font-weight:700;font-size:27px;line-height:49px;text-align:center}
.claim-left{left:50px;top:1045px;width:403px;height:149px;color:var(--white);font-weight:700;font-size:41px;line-height:42px;display:flex;align-items:center;justify-content:center;text-align:center}
.claim-right{left:453px;top:1045px;width:504px;height:149px;background:var(--navy-2);color:var(--white);font-weight:700;font-size:34px;line-height:41px;display:flex;align-items:center;padding-left:76px}
.site{font-weight:800;font-size:64px;color:var(--white);line-height:72px}

/* page two */
.top-red{left:0;top:0;width:1007px;height:297px;background:var(--red)}
.title{top:30px;font-family:'Bebas Neue',sans-serif;font-size:88px;color:var(--white);line-height:86px;letter-spacing:1px}
.mid-blue{left:0;top:570px;width:1007px;height:259px;background:var(--blue)}
.foot-red{left:0;top:1143px;width:1007px;height:151px;background:var(--red)}
.claims-card{left:48px;top:129px;width:911px;height:489px;background:var(--white)}
.claims-head{left:52px;top:133px;width:903px;height:59px;background:var(--blue);color:var(--white);font-weight:700;font-size:34px;line-height:59px;text-align:center}
.claims-list{position:absolute;top:212px;width:420px;list-style:none}
.claims-list li{position:relative;padding-left:27px;font-weight:500;font-size:19.5px;line-height:23px;color:var(--ink);height:69px}
.claims-list li:nth-child(6){height:auto;margin-top:-7px}
.claims-list li svg{position:absolute;left:0;top:4px}
.col-left{left:86px}
.col-right{left:539px}
.rally-1{top:622px;font-weight:800;font-size:30px;color:var(--yellow);line-height:40px}
.rally-2{top:662px;font-weight:700;font-size:33px;color:var(--white);line-height:40px}
.shot{top:730px;width:440px;height:202px;border:3px solid var(--white)}
.shot-beach{left:58px;background:linear-gradient(180deg,#4b6f9c 0%,#c98a5a 50%,#e9a447 58%,#556a83 80%,#8d8170 100%)}
.shot-legal{left:512px;background:linear-gradient(90deg,#2f5da3 0%,#2b4f8c 45%,#8a5e3c 70%,#5a3a24 100%)}
.lower-card{left:48px;top:935px;width:911px;height:262px;background:var(--white)}
</style>
</head>
<body>

<section class="page page-one">
  <div class="blk headline-red"></div>
  <div class="blk brand">
    <span class="brand-name">Equal Access<br>Coalition</span>
  </div>
  <h1 class="blk headline">SCANDALS ROCK<br>SEAVIEW PARK:</h1>
  <div class="blk band-blue"></div>
  <div class="photo hero-photo" role="img" aria-label="Aerial night view of the seaside amusement park with its lit wooden roller coaster and parking lot"></div>
  <p class="center alarm">Our Beloved Beachfront Is Under Attack!<br>Locals Say Seaview Park Is Out of Control</p>
  <div class="blk help-box">WE NEED YOUR HELP!</div>

  <p class="center join" style="top:760px">JOIN US &amp; SHOW YOUR SUPPORT @</p>
  <p class="center council" style="top:801px">HARBOR SHORE TOWN COUNCIL MEETING</p>
  <div class="date-row" style="top:860px">
    <svg width="50" height="50" viewBox="0 0 50 50" aria-hidden="true"><rect x="3" y="7" width="44" height="40" rx="4" fill="none" stroke="var(--blue)" stroke-width="4"/><rect x="3" y="7" width="44" height="10" fill="var(--blue)"/><rect x="12" y="2" width="4" height="10" fill="var(--blue)"/><rect x="34" y="2" width="4" height="10" fill="var(--blue)"/><g fill="var(--blue)"><rect x="10" y="22" width="6" height="5"/><rect x="20" y="22" width="6" height="5"/><rect x="30" y="22" width="6" height="5"/><rect x="10" y="31" width="6" height="5"/><rect x="20" y="31" width="6" height="5"/><rect x="30" y="31" width="6" height="5"/><rect x="10" y="39" width="6" height="4"/><rect x="20" y="39" width="6" height="4"/></g></svg>
    <span class="date-main">MAY 14</span><span class="date-year">2025</span>
    <span class="time-pill"><svg width="50" height="50" viewBox="0 0 50 50" aria-hidden="true"><circle cx="25" cy="25" r="21" fill="none" stroke="#fff" stroke-width="4"/><path d="M25 12v14l9 6" fill="none" stroke="#fff" stroke-width="4" stroke-linecap="round"/></svg>6:00 PM</span>
  </div>
  <div class="venue" style="top:934px">
    <svg width="28" height="36" viewBox="0 0 28 36" aria-hidden="true"><path d="M14 2C7.4 2 2 7.2 2 13.7 2 22 14 34 14 34s12-12 12-20.3C26 7.2 20.6 2 14 2z" fill="none" stroke="var(--sky)" stroke-width="3"/><circle cx="14" cy="13.5" r="4.5" fill="none" stroke="var(--sky)" stroke-width="3"/></svg>
    Seaview Park Community Room (Above the Arcade)
  </div>

  <div class="blk band-red-foot"></div>
  <div class="blk claim-box"></div>
  <div class="blk claim-strip">SEAVIEW PARK WAS BUILT FOR FAMILIES, NOT RAVES!</div>
  <div class="blk claim-left">Multiple<br>Lawsuits Filed:</div>
  <div class="blk claim-right">Employees &amp; Locals<br>May Be Eligible for<br>Compensation</div>
  <p class="center site" style="top:1197px">www.FixSeaviewPark.com</p>
</section>

<section class="page page-two">
  <div class="blk top-red"></div>
  <div class="blk mid-blue"></div>
  <div class="blk foot-red"></div>
  <h2 class="center title">SEAVIEW PARK OUT OF CONTRIOL?</h2>
  <div class="blk claims-card"></div>
  <div class="blk claims-head">Explosive community claims demand answers:</div>

  <ul class="claims-list col-left">
    <li><svg width="15" height="15" viewBox="0 0 16 16"><circle cx="8" cy="8" r="8" fill="var(--blue)"/><path d="M4.5 8.2l2.3 2.3 4.7-4.8" fill="none" stroke="#fff" stroke-width="2"/></svg>Accused of Running Drug and<br>Alcohol-Fueled Raves</li>
    <li><svg width="15" height="15" viewBox="0 0 16 16"><circle cx="8" cy="8" r="8" fill="var(--blue)"/><path d="M4.5 8.2l2.3 2.3 4.7-4.8" fill="none" stroke="#fff" stroke-width="2"/></svg>Illegal Raves Continue Despite City<br>Permit Denials</li>
    <li><svg width="15" height="15" viewBox="0 0 16 16"><circle cx="8" cy="8" r="8" fill="var(--blue)"/><path d="M4.5 8.2l2.3 2.3 4.7-4.8" fill="none" stroke="#fff" stroke-width="2"/></svg>Beloved Family Beachfront Turned<br>into Private Club</li>
    <li><svg width="15" height="15" viewBox="0 0 16 16"><circle cx="8" cy="8" r="8" fill="var(--blue)"/><path d="M4.5 8.2l2.3 2.3 4.7-4.8" fill="none" stroke="#fff" stroke-width="2"/></svg>100 Decibel Music Shatters Peace<br>Half a Mile Away</li>
    <li><svg width="15" height="15" viewBox="0 0 16 16"><circle cx="8" cy="8" r="8" fill="var(--blue)"/><path d="M4.5 8.2l2.3 2.3 4.7-4.8" fill="none" stroke="#fff" stroke-width="2"/></svg>Disabled Say Sound Assault Forced<br>Them Off the Beach</li>
    <li><svg width="15" height="15" viewBox="0 0 16 16"><circle cx="8" cy="8" r="8" fill="var(--blue)"/><path d="M4.5 8.2l2.3 2.3 4.7-4.8" fill="none" stroke="#fff" stroke-width="2"/></svg>Americans with Disability Act<br>Violations Appear Ignored</li>
  </ul>
  <ul class="claims-list col-right">
    <li><svg width="15" height="15" viewBox="0 0 16 16"><circle cx="8" cy="8" r="8" fill="var(--blue)"/><path d="M4.5 8.2l2.3 2.3 4.7-4.8" fill="none" stroke="#fff" stroke-width="2"/></svg>Toxic Waste Reportedly Dumped into<br>Public Storm Drains</li>
    <li><svg width="15" height="15" viewBox="0 0 16 16"><circle cx="8" cy="8" r="8" fill="var(--blue)"/><path d="M4.5 8.2l2.3 2.3 4.7-4.8" fill="none" stroke="#fff" stroke-width="2"/></svg>Employees Report Wage Theft and<br>Dangerous Conditions</li>
    <li><svg width="15" height="15" viewBox="0 0 16 16"><circle cx="8" cy="8" r="8" fill="var(--blue)"/><path d="M4.5 8.2l2.3 2.3 4.7-4.8" fill="none" stroke="#fff" stroke-width="2"/></svg>Millions in Public Revenue Possibly<br>Hidden from City</li>
    <li><svg width="15" height="15" viewBox="0 0 16 16"><circle cx="8" cy="8" r="8" fill="var(--blue)"/><path d="M4.5 8.2l2.3 2.3 4.7-4.8" fill="none" stroke="#fff" stroke-width="2"/></svg>Unpermitted Construction &amp;<br>Safety Violations</li>
    <li><svg width="15" height="15" viewBox="0 0 16 16"><circle cx="8" cy="8" r="8" fill="var(--blue)"/><path d="M4.5 8.2l2.3 2.3 4.7-4.8" fill="none" stroke="#fff" stroke-width="2"/></svg>Paint Used to Hide Construction<br>Defects</li>
    <li><svg width="15" height="15" viewBox="0 0 16 16"><circle cx="8" cy="8" r="8" fill="var(--blue)"/><path d="M4.5 8.2l2.3 2.3 4.7-4.8" fill="none" stroke="#fff" stroke-width="2"/></svg>Seaview Mayhem Ties Up Police,<br>Firetrucks and Ambulances</li>
  </ul>

  <p class="center rally-1">HELP STOP SEAVIEW BEFORE IT’S TOO LATE</p>
  <p class="center rally-2">Demand City Leaders Take Action &amp; Enforce the Lease!</p>
  <div class="blk lower-card"></div>
  <div class="blk shot shot-beach" role="img" aria-label="Lifeguard tower on the beach at sunset"></div>
  <div class="blk shot shot-legal" role="img" aria-label="Class action law book with scales of justice beside a wooden gavel"></div>

  <p class="center join" style="top:962px">JOIN US &amp; SHOW YOUR SUPPORT @</p>
  <p class="center council" style="top:1002px">HARBOR SHORE TOWN COUNCIL MEETING</p>
  <div class="date-row" style="top:1061px">
    <svg width="50" height="50" viewBox="0 0 50 50" aria-hidden="true"><rect x="3" y="7" width="44" height="40" rx="4" fill="none" stroke="var(--blue)" stroke-width="4"/><rect x="3" y="7" width="44" height="10" fill="var(--blue)"/><rect x="12" y="2" width="4" height="10" fill="var(--blue)"/><rect x="34" y="2" width="4" height="10" fill="var(--blue)"/><g fill="var(--blue)"><rect x="10" y="22" width="6" height="5"/><rect x="20" y="22" width="6" height="5"/><rect x="30" y="22" width="6" height="5"/><rect x="10" y="31" width="6" height="5"/><rect x="20" y="31" width="6" height="5"/><rect x="30" y="31" width="6" height="5"/><rect x="10" y="39" width="6" height="4"/><rect x="20" y="39" width="6" height="4"/></g></svg>
    <span class="date-main">MAY 14</span><span class="date-year">2025</span>
    <span class="time-pill"><svg width="50" height="50" viewBox="0 0 50 50" aria-hidden="true"><circle cx="25" cy="25" r="21" fill="none" stroke="#fff" stroke-width="4"/><path d="M25 12v14l9 6" fill="none" stroke="#fff" stroke-width="4" stroke-linecap="round"/></svg>6:00 PM</span>
  </div>
  <div class="venue" style="top:1134px">
    <svg width="28" height="36" viewBox="0 0 28 36" aria-hidden="true"><path d="M14 2C7.4 2 2 7.2 2 13.7 2 22 14 34 14 34s12-12 12-20.3C26 7.2 20.6 2 14 2z" fill="none" stroke="var(--sky)" stroke-width="3"/><circle cx="14" cy="13.5" r="4.5" fill="none" stroke="var(--sky)" stroke-width="3"/></svg>
    Seaview Park Community Room (Above the Arcade)
  </div>
  <p class="center site" style="top:1202px">www.FixSeaviewPark.com</p>
</section>

</body>
</html>
```